Public Adjusters Collective Business card

We need to get business card Design for our Company we are Public Adjusters in Chicago Illinois - i like to see good combination and elements from my Company Logo. as well To be an two side design
Updates

Target Market(s)

Home /Business owner Property Managers

Industry/Entity Type

Business

Contact Information for Business Card

to show the Element of our logo i will Like 3D

Font styles to use
Sans Serif

Requirements
Must have
• Logo and Element of the Logo in 3D
Nice to have
• Logo That we Provide 3D Same Colors or open for suggestions
Should not have
• unleare view -

```html
<!DOCTYPE html>
<html lang="en">
<head>
<meta charset="utf-8">
<title>Public Adjusters Collective – Business Card</title>
<link rel="stylesheet" href="https://fonts.googleapis.com/css2?family=Open+Sans:wght@400;600;700&display=swap">
<style>
  :root {
    --backdrop: #5a4a3b;
    --paper: #ffffff;
    --navy-deep: #13104f;
    --navy: #1b2a9c;
    --royal: #1f4fd8;
    --brand-blue: #1d2fb4;
    --brand-red: #d9452f;
    --panel-edge: #e25a3f;
    --ink-light: #ffffff;
    --rule: rgba(255,255,255,0.35);
  }
  * { box-sizing: border-box; margin: 0; padding: 0; }
  html, body { width: 1200px; height: 987px; overflow: hidden; }
  body {
    background: var(--backdrop);
    font-family: "Open Sans", Arial, sans-serif;
    position: relative;
  }
  .card {
    position: absolute;
    left: 293px;
    width: 615px;
    height: 352px;
    overflow: hidden;
    box-shadow: 0 3px 8px rgba(0,0,0,0.35);
  }
  .card--front { top: 130px; background: var(--paper); }
  .card--back {
    top: 505px;
    background: radial-gradient(ellipse 60% 75% at 50% 42%, var(--royal) 0%, var(--navy) 55%, var(--navy-deep) 100%);
  }

  /* Front: brand name block */
  .brand {
    position: absolute;
    left: 18px;
    top: 132px;
    width: 240px;
    text-align: center;
  }
  .brand__dot {
    display: block;
    margin: 0 auto 14px;
    width: 34px; height: 34px;
    border-radius: 50%;
    background: var(--brand-blue);
  }
  .brand__name {
    color: var(--brand-blue);
    font-weight: 700;
    font-size: 16px;
    white-space: nowrap;
  }

  .person { position: absolute; left: 37px; top: 278px; }
  .person__name {
    color: var(--brand-blue);
    font-weight: 600;
    font-size: 21px;
    letter-spacing: 0.3px;
    line-height: 1.1;
  }
  .person__title {
    color: var(--brand-red);
    font-size: 16px;
    margin-top: 4px;
  }

  .contact-panel { position: absolute; left: 326px; top: 87px; width: 289px; height: 265px; }

  .contact {
    position: absolute;
    right: 28px;
    top: 161px;
    color: var(--ink-light);
    font-size: 15.5px;
    text-align: right;
    line-height: 1;
  }
  .contact__address { margin-bottom: 10px; }
  .contact__address span { display: block; margin-bottom: 6px; }
  .contact__row {
    display: flex;
    justify-content: flex-end;
    align-items: center;
    gap: 7px;
    height: 23.5px;
  }
  .contact__row svg { width: 15px; height: 15px; fill: var(--ink-light); }

  /* Back */
  .back-brand {
    position: absolute;
    left: 0; right: 0;
    top: 112px;
    text-align: center;
  }
  .back-brand__dot {
    display: block;
    margin: 0 auto 20px;
    width: 48px; height: 48px;
    border-radius: 50%;
    background: var(--brand-red);
  }
  .back-brand__name {
    color: var(--ink-light);
    font-weight: 700;
    font-size: 26px;
  }
  .back-rule {
    position: absolute;
    left: 82px; right: 88px;
    top: 271px;
    height: 1px;
    background: linear-gradient(90deg, transparent, var(--rule) 20%, var(--rule) 80%, transparent);
  }
  .back-url {
    position: absolute;
    left: 0; right: 0;
    top: 286px;
    text-align: center;
    color: var(--ink-light);
    font-size: 16px;
    letter-spacing: 2.2px;
  }
</style>
</head>
<body>

<section class="card card--front" aria-label="Business card front">
  <div class="brand">
    <span class="brand__dot"></span>
    <p class="brand__name">Public Adjusters Collective</p>
  </div>

  <div class="person">
    <p class="person__name">DANIEL REYES</p>
    <p class="person__title">CEO/Founder</p>
  </div>

  <svg class="contact-panel" viewBox="0 0 289 265" preserveAspectRatio="none" aria-hidden="true">
    <defs>
      <radialGradient id="panelFill" cx="60%" cy="40%" r="75%">
        <stop offset="0" stop-color="#2a3fd0"/>
        <stop offset="0.6" stop-color="#1a2391"/>
        <stop offset="1" stop-color="#14105a"/>
      </radialGradient>
    </defs>
    <path d="M49 265 C 22 200, 2 130, 0 82 C 80 44, 170 18, 248 0 L 289 0 L 289 265 Z" fill="var(--panel-edge)"/>
    <path d="M61 265 C 34 202, 14 136, 12 89 C 88 54, 174 28, 250 11 L 289 11 L 289 265 Z" fill="url(#panelFill)"/>
  </svg>

  <div class="contact">
    <div class="contact__address">
      <span>4120 Larkspur Avenue</span>
      <span>Chicago, Illinois 60614</span>
    </div>
    <div class="contact__row">312 555 0148
      <svg viewBox="0 0 16 16"><path d="M3.6 1.2l2.4 2.6-1.3 2.1c.8 1.8 2.2 3.3 4 4.2l2.1-1.3 2.6 2.4-1.2 2.4C7.2 13.7 2.3 8.8 1.2 3.8z"/></svg>
    </div>
    <div class="contact__row">312 555 0172
      <svg viewBox="0 0 16 16"><path d="M4.5 1h7v14h-7zM5.8 2.5v9.5h4.4V2.5zM7.3 13h1.4v1H7.3z" fill-rule="evenodd"/></svg>
    </div>
    <div class="contact__row">312 555 0193
      <svg viewBox="0 0 16 16"><path d="M4 1h8v4H4zM1 6h14v6h-3v3H4v-3H1zM5 10v4h6v-4z" fill-rule="evenodd"/></svg>
    </div>
    <div class="contact__row">hello@qpacollective.com
      <svg viewBox="0 0 16 16"><path d="M1 3.5h14v9H1zM2.2 4.6L8 9l5.8-4.4v7H2.2z" fill-rule="evenodd"/></svg>
    </div>
    <div class="contact__row">www.qpacollective.com
      <svg viewBox="0 0 16 16"><path d="M8 1a7 7 0 1 0 0 14A7 7 0 0 0 8 1zm-1 2.3c-.6 1-1.6 1.5-2.4 2.4.6.9.2 1.9 1.2 2.4.9.4 1.3 1.4.8 2.5-.3.7 0 1.6.5 2.1A5.6 5.6 0 0 1 7 3.3zm2.2.1a5.6 5.6 0 0 1 3.9 7.4c-.6-.6-1.6-.4-2-1.3-.4-1 .6-1.6 0-2.5-.6-.7-1.8-.3-2.1-1.3-.2-.9.6-1.5.2-2.3z"/></svg>
    </div>
  </div>
</section>

<section class="card card--back" aria-label="Business card back">
  <div class="back-brand">
    <span class="back-brand__dot"></span>
    <p class="back-brand__name">Public Adjusters Collective</p>
  </div>
  <div class="back-rule"></div>
  <p class="back-url">www.PublicAdjustersCollective.com</p>
</section>

</body>
</html>
```